Brenlow Estates Website and Logo Design

We need a new logo and website designed for 'Brenlow Estates Ltd', which is a well established Guernsey property holding company founded in 1934.

The company does not currently have a website. The new website should be similar in style and layout to https://www.quorvanhall.example/.

Target Market(s)

Industry, Media, Tenants

Industry/Entity Type

Property Management

Logo Text

BEL OR Brenlow Estates Ltd OR BE

Coding

Coded - Design and coding required

Number of Pages Required

4 page

Font styles to use
Other font styles liked:
• Helvetica

Requirements
Must have
• The logo laying over the picture (like https://www.quorvanhall.example/).
• Big pictures on homepage (like https://www.quorvanhall.example/)

```html
<!DOCTYPE html>
<html lang="en">
<head>
<meta charset="utf-8">
<title>Brenlow Estates Ltd</title>
<link href="https://fonts.googleapis.com/css2?family=Alegreya+SC:ital,wght@0,400;0,500;1,400&family=Arimo:wght@400;700&display=swap" rel="stylesheet">
<style>
:root{
  --blue:#1a9de6;
  --blue-deep:#0b7fcf;
  --blue-dark:#0867b3;
  --ink:#222;
  --grey-text:#6b6b6b;
  --panel:#eeeeee;
  --white:#fff;
  --serif:'Alegreya SC', Georgia, serif;
  --sans:'Arimo', Helvetica, Arial, sans-serif;
}
*{box-sizing:border-box;margin:0;padding:0}
html,body{width:1200px;height:3346px;overflow:hidden}
body{font-family:var(--sans);color:var(--ink);background:var(--white);position:relative}
.abs{position:absolute}
a{color:inherit;text-decoration:none}

/* header */
.site-header{position:absolute;left:0;top:0;width:1200px;height:107px;background:var(--white)}
.brand{left:78px;top:14px;display:flex;align-items:center;gap:14px}
.brand-mark{width:84px;height:84px;border:3px solid var(--blue-dark);border-radius:50%}
.brand-name{font-family:var(--serif);font-weight:500;color:var(--blue-dark);font-size:34px;line-height:34px}
.topbar-mail{left:625px;top:0;width:255px;height:36px;display:flex;align-items:center;gap:10px;font-size:15px;color:var(--blue-dark)}
.topbar-phone{left:880px;top:0;width:290px;height:38px;background:var(--blue);color:var(--white);border-radius:0 0 0 18px;display:flex;align-items:center;gap:12px;padding-left:40px;font-size:16px}
.main-nav{left:490px;top:57px;display:flex;align-items:center;font-size:17px}
.main-nav a{height:50px;line-height:50px;padding:0 21px;margin-right:18px;color:#222}
.main-nav a.active{background:var(--blue);color:var(--white);border-radius:3px 3px 0 0}
.search{left:1098px;top:70px}

/* hero */
.hero{position:absolute;left:0;top:107px;width:1200px;height:573px;background:linear-gradient(180deg,#3c5d99 0%,#6b86bb 35%,#8ea3c9 50%,#4b6899 62%,#203b63 100%)}
.hero-title{right:78px;top:175px;font-family:var(--serif);font-size:62px;color:var(--white);letter-spacing:1px;text-align:right}
.hero-text{right:78px;top:262px;width:720px;text-align:right;color:var(--white);font-size:17px;line-height:30px}
.btn{display:inline-block;background:var(--blue);color:var(--white);font-family:var(--serif);text-align:center;border-radius:3px}
.hero-btn{right:78px;top:335px;width:188px;height:60px;line-height:60px;font-size:22px}
.hero-arrow{top:265px}

/* welcome */
.welcome{position:absolute;left:0;top:680px;width:1200px;height:252px;background:var(--blue);color:var(--white);text-align:center}
.welcome h1{font-family:var(--serif);font-weight:400;font-size:44px;margin-top:38px}
.welcome p{width:960px;margin:14px auto 0;font-size:14.5px;line-height:29px}

/* eras */
.era{position:absolute;top:995px;width:333px;height:420px;background:var(--panel);border-bottom:4px solid var(--blue)}
.era h2{height:62px;line-height:62px;background:var(--blue);color:var(--white);font-family:var(--serif);font-weight:400;text-align:center;font-size:26px}
.era .photo{height:208px}
.era p{padding:18px 28px 0;text-align:center;color:var(--grey-text);font-size:14.5px;line-height:29px}
.era svg{display:block;margin:4px auto 0}

/* why */
.why{position:absolute;left:0;top:1481px;width:1200px;height:426px;background:linear-gradient(180deg,#2a9ae2,#1e8fdc);color:var(--white)}
.video{left:76px;top:134px;width:334px;height:230px;background:#1d1d1d;padding:5px}
.video .photo{height:196px;background:linear-gradient(180deg,#5d8fcf 0%,#9dbde0 35%,#c2b69a 55%,#3f7a91 75%,#2b5f78 100%)}
.video .bar{height:20px;display:flex;align-items:center;gap:8px;padding:0 6px}
.video .track{flex:1;height:3px;background:#666}
.why h2{left:488px;top:60px;font-family:var(--serif);font-weight:400;font-size:44px}
.why p{left:490px;width:640px;font-size:14px;line-height:28px}
.why .know{left:490px;top:309px;width:168px;height:54px;line-height:52px;border:1.5px solid var(--white);border-radius:3px;font-family:var(--serif);font-size:22px;text-align:center}

/* projects */
.projects{position:absolute;left:0;top:1907px;width:1200px;height:703px;background:#efefef}
.section-title{position:absolute;left:0;width:1200px;text-align:center;font-family:var(--serif);font-weight:400;color:var(--blue-deep);font-size:44px}
.tile{position:absolute;width:333px;height:208px}
.tile-feature{background:var(--blue);color:var(--white);text-align:center;padding-top:50px}
.tile-feature h3{font-family:var(--serif);font-weight:500;font-size:26px;color:#1a2a3a}
.tile-feature p{font-size:14px;line-height:23px;width:250px;margin:8px auto 0}
.view-all{left:517px;top:586px;width:166px;height:56px;line-height:56px;font-size:22px}

/* news */
.news-card{position:absolute;top:2730px;width:251px}
.news-card .photo{height:168px}
.news-card h3{margin-top:16px;font-family:var(--serif);font-style:italic;font-weight:400;font-size:18px;color:#222}
.news-card .meta{margin-top:8px;font-size:13.5px;font-style:italic;color:var(--blue);display:flex;align-items:center;gap:8px}
.news-card p{margin-top:6px;font-size:13.5px;line-height:27px;color:var(--grey-text)}

/* footer */
.site-footer{position:absolute;left:0;top:3111px;width:1200px;height:235px;background:linear-gradient(180deg,#2b9be3,#1b8cd9);color:var(--white)}
.foot-nav{left:76px;top:29px;display:flex;align-items:center;font-size:15px}
.foot-nav a{height:42px;line-height:42px;padding:0 26px;margin-right:22px}
.foot-nav a.active{border:1.5px solid var(--white);border-radius:2px}
.social{left:1022px;top:42px;display:flex;gap:22px}
.social span{width:18px;height:18px;border-radius:50%;background:var(--white);display:block}
.foot-label{left:80px;top:120px;font-family:var(--serif);font-size:19px}
.contact-item{top:158px;display:flex;align-items:center;gap:18px;font-size:14px;line-height:20px}
.icon-round{width:40px;height:40px;border-radius:50%;display:flex;align-items:center;justify-content:center;flex:none}
.icon-solid{background:var(--white)}
.icon-line{border:1.5px solid var(--white)}
.copyright{left:996px;top:164px;font-size:13px;line-height:20px;color:#d8ecfb}
.copyright b{color:var(--white)}
</style>
</head>
<body>

<header class="site-header">
  <div class="abs brand">
    <span class="brand-mark"></span>
    <span class="brand-name">Brenlow Estates<br>Ltd</span>
  </div>
  <div class="abs topbar-mail">
    <svg width="18" height="14" viewBox="0 0 18 14"><rect x="1" y="1" width="16" height="12" fill="#0867b3"/><path d="M1 1l8 7 8-7" stroke="#fff" stroke-width="1.5" fill="none"/></svg>
    info@BrenlowEstates.com
  </div>
  <div class="abs topbar-phone">
    <svg width="18" height="18" viewBox="0 0 24 24"><path fill="#fff" d="M6.6 10.8a15 15 0 0 0 6.6 6.6l2.2-2.2c.3-.3.7-.4 1-.2 1.1.4 2.3.6 3.6.6.6 0 1 .4 1 1V20c0 .6-.4 1-1 1A17 17 0 0 1 3 4c0-.6.4-1 1-1h3.5c.6 0 1 .4 1 1 0 1.3.2 2.5.6 3.6.1.3 0 .7-.2 1z"/></svg>
    +1 555 014 7890
  </div>
  <nav class="abs main-nav">
    <a class="active" href="#">HOME</a>
    <a href="#">ABOUT</a>
    <a href="#">PROJECTS</a>
    <a href="#">NEWS</a>
    <a href="#">CONTACT</a>
  </nav>
  <svg class="abs search" width="24" height="24" viewBox="0 0 24 24"><circle cx="10" cy="10" r="7" stroke="#1a9de6" stroke-width="3" fill="none"/><path d="M15 15l6 6" stroke="#1a9de6" stroke-width="3.5" stroke-linecap="round"/></svg>
</header>

<section class="hero" role="img" aria-label="Marina at dusk with moored sailing yachts and calm blue water">
  <svg class="abs hero-arrow" style="left:28px" width="16" height="26" viewBox="0 0 16 26"><path d="M13 2L3 13l10 11" stroke="#fff" stroke-width="2" fill="none"/></svg>
  <svg class="abs hero-arrow" style="right:28px" width="16" height="26" viewBox="0 0 16 26"><path d="M3 2l10 11L3 24" stroke="#fff" stroke-width="2" fill="none"/></svg>
  <h1 class="abs hero-title">BRENLOW ESTATES LTD</h1>
  <p class="abs hero-text">Brenlow Estates Limited (BEL) is a family-owned Guernsey property holding company. It purchases properties that are considered to have potential for development .</p>
  <a class="abs btn hero-btn" href="#">CONTACT US</a>
</section>

<section class="welcome">
  <h1>Welcome to Brenlow Estates Ltd</h1>
  <p>Brenlow Estates Limited (BEL) is a family-owned Guernsey property holding company. It purchases properties that are considered to have potential for development either through refurbishment or by obtaining planning permission to change its classification from, for example, industrial premises to offices or retail outlets, or by the marriage value of buying.</p>
  <svg style="margin-top:10px" width="20" height="22" viewBox="0 0 20 22"><path d="M3 3l7 7 7-7M3 11l7 7 7-7" stroke="#fff" stroke-width="2.2" fill="none"/></svg>
</section>

<article class="era" style="left:78px">
  <h2>Yesterday</h2>
  <div class="photo" role="img" aria-label="Harbour town with boats on blue water" style="background:linear-gradient(180deg,#9fc4ea 0%,#d9e6ef 30%,#a9b3a0 45%,#3d7f94 60%,#2b6e86 100%)"></div>
  <p>BEL was founded in 1934 by Edwin Brenlow to manage both his own extensive investments and his property portfolio.</p>
  <svg width="16" height="16" viewBox="0 0 16 16"><path d="M2 2l6 6 6-6M2 8l6 6 6-6" stroke="#1a9de6" stroke-width="1.8" fill="none"/></svg>
</article>
<article class="era" style="left:433px">
  <h2>Today</h2>
  <div class="photo" role="img" aria-label="City skyline at sunset across a harbour" style="background:linear-gradient(180deg,#5a7fb8 0%,#e7a07a 30%,#6b5a66 48%,#2d3b55 62%,#a06a4a 80%,#2a3650 100%)"></div>
  <p>The Brenlow family has steadily built on the foundations set out by the founder and each generation develops and.</p>
  <svg width="16" height="16" viewBox="0 0 16 16"><path d="M2 2l6 6 6-6M2 8l6 6 6-6" stroke="#1a9de6" stroke-width="1.8" fill="none"/></svg>
</article>
<article class="era" style="left:789px">
  <h2>Tomorrow</h2>
  <div class="photo" role="img" aria-label="Coastal town on a hillside above a marina" style="background:linear-gradient(180deg,#7aaee6 0%,#bcd5ee 25%,#a7aaa0 45%,#5e8f8f 62%,#2f6f82 100%)"></div>
  <p>In keeping with its past project development philosophy, its intrinsic understanding of the local property market and the.</p>
  <svg width="16" height="16" viewBox="0 0 16 16"><path d="M2 2l6 6 6-6M2 8l6 6 6-6" stroke="#1a9de6" stroke-width="1.8" fill="none"/></svg>
</article>

<section class="why">
  <div class="abs video">
    <div class="photo" role="img" aria-label="Video still of a harbour town with moored boats"></div>
    <div class="bar">
      <svg width="10" height="10" viewBox="0 0 10 10"><rect x="1" y="1" width="3" height="8" fill="#ccc"/><rect x="6" y="1" width="3" height="8" fill="#ccc"/></svg>
      <span class="track"></span>
      <svg width="12" height="10" viewBox="0 0 12 10"><path d="M1 3h3l4-3v10L4 7H1z" fill="#ccc"/></svg>
      <svg width="10" height="10" viewBox="0 0 10 10"><rect x="1" y="1" width="8" height="8" stroke="#ccc" fill="none"/></svg>
    </div>
  </div>
  <h2 class="abs">Why Guernsey?</h2>
  <p class="abs" style="top:120px">The Bailiwick of Guernsey is a British Crown dependency in the English Channel. The benefit of establishing a company in Guernsey is the island's low tax jurisdiction since there are no capital taxes and no corporation taxes for many companies.</p>
  <p class="abs" style="top:212px">Consequently since the 1980s the island's development as an ideal financial centre for the establishment of institutions and banks has thrived. There are currently more than 160 companies registered with the Bailiwick Finance Registry.</p>
  <a class="abs know" href="#">KNOW MORE</a>
</section>

<section class="projects">
  <h2 class="section-title" style="top:58px">Our Projects</h2>
  <div class="tile" style="left:78px;top:133px;background:linear-gradient(180deg,#4a5f8e 0%,#9aa8c6 40%,#b89a7a 62%,#4a4e6a 100%)" role="img" aria-label="Rendering of modern towers on a waterfront"></div>
  <div class="tile tile-feature" style="left:433px;top:133px">
    <h3>PROJECT TITLE</h3>
    <p>Lorem Ipsum is simply dummy text of the printing and typesetting industry</p>
    <svg style="margin-top:6px" width="16" height="16" viewBox="0 0 16 16"><path d="M2 2l6 6 6-6M2 8l6 6 6-6" stroke="#1a2a3a" stroke-width="1.8" fill="none"/></svg>
  </div>
  <div class="tile" style="left:789px;top:133px;background:linear-gradient(180deg,#8fb6e0 0%,#c9d4dc 35%,#9c9a8c 55%,#5a7f8c 75%,#3b6577 100%)" role="img" aria-label="Harbour town with houses along the quay"></div>
  <div class="tile" style="left:78px;top:361px;background:linear-gradient(180deg,#2d3f6a 0%,#e07a2e 40%,#f2a33a 52%,#3b3a4a 72%,#1f2740 100%)" role="img" aria-label="Fishing boat in harbour under an orange sunset"></div>
  <div class="tile" style="left:433px;top:361px;background:linear-gradient(180deg,#9fbfd8 0%,#7d7f78 30%,#6f8ea0 55%,#3d6f8c 100%)" role="img" aria-label="Small boats beside a stone harbour wall"></div>
  <div class="tile" style="left:789px;top:361px;background:linear-gradient(180deg,#6ea2de 0%,#c4d0d6 35%,#8c9a8c 55%,#3e7890 75%,#2c5f78 100%)" role="img" aria-label="Marina with sailing boats and waterfront buildings"></div>
  <a class="abs btn view-all" href="#">VIEW ALL</a>
</section>

<section>
  <h2 class="section-title" style="top:2668px">Latest News</h2>
  <article class="news-card" style="left:76px">
    <div class="photo" role="img" aria-label="Yachts reflected in a marina at sunset" style="background:linear-gradient(180deg,#4c6ea8 0%,#d89466 45%,#6b7aa6 65%,#2f4a7a 100%)"></div>
    <h3>Lorem ipsum is simple text</h3>
    <div class="meta"><svg width="14" height="14" viewBox="0 0 14 14"><rect x="1" y="2" width="12" height="11" stroke="#1a9de6" fill="none" stroke-width="1.4"/><path d="M1 5h12" stroke="#1a9de6" stroke-width="1.4"/></svg>Posted by 1 Dec,</div>
    <p>Lorem Ipsum is simply dummy text of the printing and typesetting industry Lorem Ipsum has.</p>
  </article>
  <article class="news-card" style="left:342px">
    <div class="photo" role="img" aria-label="Aerial view of a harbour and town" style="background:linear-gradient(180deg,#8ab0d6 0%,#b8c2c8 40%,#3f7aa6 70%,#245d8c 100%)"></div>
    <h3>Lorem ipsum is simple text</h3>
    <div class="meta"><svg width="14" height="14" viewBox="0 0 14 14"><rect x="1" y="2" width="12" height="11" stroke="#1a9de6" fill="none" stroke-width="1.4"/><path d="M1 5h12" stroke="#1a9de6" stroke-width="1.4"/></svg>Posted by 1 Dec,</div>
    <p>Lorem Ipsum is simply dummy text of the printing and typesetting industry Lorem Ipsum has.</p>
  </article>
  <article class="news-card" style="left:607px">
    <div class="photo" role="img" aria-label="Fishing boat in harbour under an orange sunset" style="background:linear-gradient(180deg,#2d3f6a 0%,#e07a2e 40%,#f2a33a 52%,#3b3a4a 72%,#1f2740 100%)"></div>
    <h3>Lorem ipsum is simple text</h3>
    <div class="meta"><svg width="14" height="14" viewBox="0 0 14 14"><rect x="1" y="2" width="12" height="11" stroke="#1a9de6" fill="none" stroke-width="1.4"/><path d="M1 5h12" stroke="#1a9de6" stroke-width="1.4"/></svg>Posted by 1 Dec,</div>
    <p>Lorem Ipsum is simply dummy text of the printing and typesetting industry Lorem Ipsum has.</p>
  </article>
  <article class="news-card" style="left:873px">
    <div class="photo" role="img" aria-label="Marina with yachts at blue dusk" style="background:linear-gradient(180deg,#3c5d99 0%,#8ea3c9 45%,#4b6899 65%,#203b63 100%)"></div>
    <h3>Lorem ipsum is simple text</h3>
    <div class="meta"><svg width="14" height="14" viewBox="0 0 14 14"><rect x="1" y="2" width="12" height="11" stroke="#1a9de6" fill="none" stroke-width="1.4"/><path d="M1 5h12" stroke="#1a9de6" stroke-width="1.4"/></svg>Posted by 1 Dec,</div>
    <p>Lorem Ipsum is simply dummy text of the printing and typesetting industry Lorem Ipsum has.</p>
  </article>
</section>

<footer class="site-footer">
  <nav class="abs foot-nav">
    <a class="active" href="#">Home</a>
    <a href="#">About</a>
    <a href="#">Projects</a>
    <a href="#">News</a>
    <a href="#">Contact Us</a>
  </nav>
  <div class="abs social"><span></span><span></span><span></span></div>
  <div class="abs foot-label">Contct US</div>
  <div class="abs contact-item" style="left:76px">
    <span class="icon-round icon-solid"><svg width="16" height="20" viewBox="0 0 16 20"><path d="M8 1a6 6 0 0 0-6 6c0 5 6 12 6 12s6-7 6-12a6 6 0 0 0-6-6z" fill="#1a9de6"/><circle cx="8" cy="7" r="2.2" fill="#fff"/></svg></span>
    <span>101 - Lorem Ipsum is simple<br>dummy text of print.</span>
  </div>
  <div class="abs contact-item" style="left:355px">
    <span class="icon-round icon-line"><svg width="14" height="20" viewBox="0 0 14 20"><rect x="1" y="1" width="12" height="18" rx="2" stroke="#fff" stroke-width="1.6" fill="none"/><circle cx="7" cy="16" r="1" fill="#fff"/></svg></span>
    <span>555 014 7890</span>
  </div>
  <div class="abs contact-item" style="left:610px">
    <span class="icon-round icon-line"><svg width="18" height="14" viewBox="0 0 18 14"><rect x="1" y="1" width="16" height="12" stroke="#fff" stroke-width="1.5" fill="none"/><path d="M1 1l8 7 8-7" stroke="#fff" stroke-width="1.5" fill="none"/></svg></span>
    <span>info@BrenlowEstates.com</span>
  </div>
  <p class="abs copyright">&copy;<b>Brenlow Estates Ltd</b> - 2016. All<br>Rights Reserved</p>
</footer>

</body>
</html>
```